Commercial Real Estate

We need a business card design for a new commercial real estate business that specializes in apartment building brokerage. Not individual units but the entire complex. We find and represent the owners existing buildings and well as new buyers for those buildings. The design should convey trust, integrity, knowledge and growth. It should be easily read.

Target Market(s)

40 to 65 years old

Industry/Entity Type

Real Estate

```html
<!DOCTYPE html>
<html lang="en">
<head>
<meta charset="utf-8">
<title>Halvern Business Card</title>
<link rel="stylesheet" href="https://fonts.googleapis.com/css2?family=Noto+Sans:wght@400;700&display=swap">
<style>
  :root {
    --bg: #e4e6e8;
    --card: #f4f5f5;
    --ink: #4a5656;
    --teal: #5ab4b4;
    --white: #ffffff;
    --pattern-a: #e9ecee;
    --pattern-b: #d6dde1;
  }
  html, body {
    margin: 0;
    padding: 0;
    width: 1200px;
    height: 720px;
    overflow: hidden;
    background: var(--bg);
    font-family: "Noto Sans", Verdana, sans-serif;
  }
  .card {
    position: absolute;
    left: 120px;
    top: 86px;
    width: 960px;
    height: 548px;
    background: var(--card);
    box-shadow: 0 6px 24px rgba(0,0,0,0.12);
    overflow: hidden;
    color: var(--ink);
  }
  .building-art {
    position: absolute;
    right: 0;
    top: 0;
    width: 340px;
    height: 230px;
    background: linear-gradient(160deg, var(--pattern-a), var(--pattern-b));
  }
  .brand-name {
    position: absolute;
    left: 40px;
    top: 92px;
    margin: 0;
    font-size: 64px;
    font-weight: 400;
    letter-spacing: 2px;
    color: var(--ink);
  }
  .name-band {
    position: absolute;
    left: 0;
    top: 230px;
    width: 100%;
    height: 58px;
    background: var(--teal);
  }
  .person-name {
    position: absolute;
    left: 40px;
    top: 8px;
    margin: 0;
    font-size: 34px;
    font-weight: 700;
    letter-spacing: 1px;
    color: var(--white);
  }
  .job-title {
    position: absolute;
    left: 40px;
    top: 302px;
    margin: 0;
    font-size: 24px;
  }
  .contact-list {
    position: absolute;
    left: 40px;
    top: 362px;
    margin: 0;
    padding: 0;
    list-style: none;
    font-size: 24px;
    line-height: 38px;
  }
  .contact-list li {
    display: flex;
    align-items: center;
    gap: 14px;
  }
  .contact-list svg {
    width: 24px;
    height: 24px;
    fill: var(--ink);
  }
  .address {
    position: absolute;
    right: 40px;
    top: 300px;
    margin: 0;
    font-style: normal;
    font-size: 24px;
    line-height: 36px;
    text-align: right;
  }
</style>
</head>
<body>
  <div class="card">
    <div class="building-art" role="img" aria-label="Faint illustration of an apartment building facade"></div>

    <p class="brand-name">HALVERN</p>

    <div class="name-band">
      <p class="person-name">MARK ELLISON</p>
    </div>

    <p class="job-title">Managing Director</p>

    <ul class="contact-list">
      <li>
        <svg viewBox="0 0 24 24" aria-hidden="true"><path d="M3 9c0-3 4-5 9-5s9 2 9 5v2h-5V9H8v2H3z M6 12h12l2 8H4z"/><circle cx="12" cy="16" r="2.2" fill="#f4f5f5"/></svg>
        <span>00 00 00 00 00</span>
      </li>
      <li>
        <svg viewBox="0 0 24 24" aria-hidden="true"><path d="M2 5h20v14H2z"/><path d="M2 5l10 8 10-8" fill="none" stroke="#f4f5f5" stroke-width="1.8"/></svg>
        <span>mark@halvern.com</span>
      </li>
      <li>
        <svg viewBox="0 0 24 24" aria-hidden="true"><circle cx="12" cy="12" r="10"/><g fill="none" stroke="#f4f5f5" stroke-width="1.4"><ellipse cx="12" cy="12" rx="4" ry="10"/><path d="M2 12h20M4 7h16M4 17h16"/></g></svg>
        <span>www.halvern.com</span>
      </li>
    </ul>

    <address class="address">PO. BOX 1000<br>Land dummy, dummy City</address>
  </div>
</body>
</html>
```